Create the ONLY Supplement line for Male Entrepreneurs! (Verity Nine MD)

I need a label designed for a new supplement brand that I am launching.

There are five products so need a design that I can simply change the wording for each individual product

The brand name is called verity nine MD. The focus is male entrepreneurial health.

Target audience is men 35 to 55.

Concepts: the healthier you are in body the more money you will make in business.

Concept to copy: I want to make a clean minimalistic label mimicking Lansworth MD (google it and you'll see what I mean)

Target Market(s)

male entrepreneurs 35-55

Industry/Entity Type

Health Supplement

Colors

Designer to choose colors to be used in the design.

Requirements
Must have
• Modern classy design, similar to Lansworth MD.
Nice to have
• Highlight that the supplement is Doctor Approved.
Should not have
• No loud colors. Present it as high class.

```html
<!DOCTYPE html>
<html lang="en">
<head>
<meta charset="utf-8">
<title>Verity nine MD — Immunity Support Label</title>
<link rel="stylesheet" href="https://fonts.googleapis.com/css2?family=Montserrat:wght@400;500&display=swap">
<style>
  :root {
    --backdrop: #c2abab;
    --label: #e7dcdf;
    --label-edge: #ddd0d4;
    --wine: #6e2a3c;
    --wine-deep: #5a1c2e;
    --wine-soft: #7d4556;
    --mark-faint: #d6c8cc;
    --on-wine: #f3e8ec;
  }
  * { box-sizing: border-box; margin: 0; padding: 0; }
  html, body {
    width: 800px;
    height: 1200px;
    overflow: hidden;
    background: var(--backdrop);
  }
  .canvas {
    position: relative;
    width: 800px;
    height: 1200px;
    background: var(--backdrop);
  }
  .label {
    position: absolute;
    left: 80px;
    top: 95px;
    width: 640px;
    height: 1010px;
    background: linear-gradient(90deg, var(--label-edge) 0%, var(--label) 30%, var(--label) 70%, var(--label-edge) 100%);
    overflow: hidden;
  }
  .label__mark-faint {
    position: absolute;
    left: 0;
    top: 0;
    width: 640px;
    height: 1010px;
  }
  .brand {
    position: absolute;
    left: 30px;
    top: 440px;
    font-family: "Montserrat", Arial, sans-serif;
    font-weight: 400;
    font-size: 50px;
    line-height: 1;
    letter-spacing: 1px;
    color: var(--wine-soft);
  }
  .rule {
    position: absolute;
    height: 1.5px;
    background: var(--wine-soft);
  }
  .rule--brand { left: 30px; top: 507px; width: 551px; }
  .rule--audience { left: 39px; top: 767px; width: 510px; }
  .product-name {
    position: absolute;
    left: 31px;
    top: 524px;
    font-family: "Montserrat", Arial, sans-serif;
    font-weight: 400;
    font-size: 27px;
    line-height: 1;
    letter-spacing: 4.5px;
    color: var(--wine-soft);
  }
  .male-icon {
    position: absolute;
    left: 44px;
    top: 610px;
    width: 92px;
    height: 92px;
  }
  .audience {
    position: absolute;
    left: 39px;
    top: 730px;
    font-family: "Montserrat", Arial, sans-serif;
    font-weight: 400;
    font-size: 29px;
    line-height: 1;
    letter-spacing: 2.5px;
    color: var(--wine-soft);
  }
  .count {
    position: absolute;
    left: 39px;
    top: 776px;
    font-family: "Montserrat", Arial, sans-serif;
    font-weight: 500;
    font-size: 26px;
    line-height: 1;
    letter-spacing: 1.5px;
    color: var(--wine-soft);
  }
  .approval-band {
    position: absolute;
    left: 0;
    top: 835px;
    width: 640px;
    height: 103px;
    background: linear-gradient(90deg, var(--wine-soft) 0%, var(--wine) 50%, var(--wine-deep) 100%);
    display: flex;
    align-items: center;
    justify-content: center;
  }
  .approval-band__text {
    font-family: "Montserrat", Arial, sans-serif;
    font-weight: 400;
    font-size: 22px;
    letter-spacing: 1.6px;
    color: var(--on-wine);
  }
</style>
</head>
<body>
  <main class="canvas">
    <section class="label">
      <svg class="label__mark-faint" viewBox="0 0 640 1010" aria-hidden="true">
        <circle cx="437" cy="730" r="100" fill="none" stroke="var(--mark-faint)" stroke-width="40"/>
        <line x1="505" y1="660" x2="612" y2="565" stroke="var(--mark-faint)" stroke-width="40"/>
        <polyline points="495,555 625,555 625,670" fill="none" stroke="var(--mark-faint)" stroke-width="36"/>
      </svg>

      <h1 class="brand">Verity nine MD</h1>
      <div class="rule rule--brand"></div>
      <p class="product-name">IMMUNITY SUPPORT</p>

      <svg class="male-icon" viewBox="0 0 92 92" aria-label="Male symbol">
        <circle cx="34" cy="58" r="24" fill="none" stroke="var(--wine)" stroke-width="9"/>
        <line x1="52" y1="40" x2="80" y2="12" stroke="var(--wine)" stroke-width="9"/>
        <polyline points="56,10 82,10 82,36" fill="none" stroke="var(--wine)" stroke-width="9"/>
      </svg>

      <p class="audience">SUPPLEMENT FOR MEN</p>
      <div class="rule rule--audience"></div>
      <p class="count">90 softgel</p>

      <div class="approval-band">
        <p class="approval-band__text">SUPPLEMENT IS DOCTOR APPROVED</p>
      </div>
    </section>
  </main>
</body>
</html>
```